Business Name: DM Space Arranging Pty Ltd

Business Type: Professional Home Styling and Minor Renovation Business

Logo: Attached is the logo that has been created.
I always envisaged the logo in the middle of the business card with my full name underneath it.

Marnie Tulloch B.Com LMR HTV
Property Stylist & Project Manager

Include dot points of services
Staging Houses for Sale
Minor Home Renovations
Home Styling & Project Management
Re-Designing Living Spaces to Aid the Disabled

Somewhere on the card I would like to incorporate
"Property Styling and Cosmetic Renovations"

Colour Scheme:
Gloss black business card, with white and then
Gold or Silver as the highlight colours.

Incorporate a small amount of yellow only if possible to make it pop. If this really doesn’t work it doesn’t have to be used. Also l like the colour teal if that needs to be used as a contrast colour.

Feel/Themes
• I love antique chairs, regal expensive looking furniture mixed with modern homes (this is the unique style I want to sell) antique and modern mix that looks high class as well as modern and fresh, targeting an executive market.
• I want to use an orchid as a trademark throughout the course of my work, not sure if this can somehow be incorporated? Also really like crowns to give that regal/antique feel and then something else to give that modern twist (I don’t know what the something else could be)
• Wall Paper Look (on a portion of it not all of it, like a French look)
• Overall feel - A very deluxe and professional feel with a little bit of creative flare.

I hope this helps create a bit of a picture.

Is it ok that I call you tomorrow morning? My mobile number is 0438 926 574 if you have any questions for me in the meantime.

Target Market(s)

High Quality Executive Market - People selling homes

Industry/Entity Type

Business

Contact Information for Business Card

Include dot points of services:
Staging Houses for Sale
Minor Home Renovations

Font styles to use
Serif
Script

Colors
33b8a4
fbed22

Requirements
Must have
• Marnie Tulloch B.Com LMR HTV
• Property Stylist & Project Manager
• LMR and HTV Logos on the card
• "Dramatically increase the value of your property"
Nice to have
• Colour Scheme:
• Gloss black business card, with white and then
• Gold or Silver as the highlight colours.
• Incorporate a small amount of yellow only if possible to make it pop. If this really doesn’t work it doesn’t have to be used. Also l like the colour teal if that needs to be used as a contrast colour.
• Also like teal as a highlight colour.

```html
<!DOCTYPE html>
<html lang="en">
<head>
<meta charset="utf-8">
<title>DM Space Arranging Pty Ltd — Business Card</title>
<link rel="stylesheet" href="https://fonts.googleapis.com/css2?family=Tinos:wght@400&family=Pinyon+Script&display=swap">
<style>
  :root {
    --backdrop: #1c1c1e;
    --card-white: #ffffff;
    --ink: #2a2a2a;
    --gloss-black: #0d0d0d;
    --gold-light: #f3d98a;
    --gold: #c9a24a;
    --gold-deep: #8a6a22;
    --ornament: #ececec;
  }
  * { box-sizing: border-box; margin: 0; padding: 0; }
  html, body { width: 1200px; height: 852px; overflow: hidden; }
  body {
    background: var(--backdrop);
    font-family: "Tinos", "Times New Roman", serif;
    color: var(--ink);
    position: relative;
  }
  .card {
    position: absolute;
    width: 520px;
    height: 300px;
    background: var(--card-white);
    border-radius: 10px;
    overflow: hidden;
    box-shadow: 0 18px 40px rgba(0,0,0,.55);
  }
  .card-front { left: 70px; top: 110px; }
  .card-back  { left: 610px; top: 440px; }
  .card-art { position: absolute; inset: 0; width: 100%; height: 100%; }

  .ornament {
    position: absolute;
    border-radius: 50%;
    background: radial-gradient(ellipse at center, var(--ornament) 0%, rgba(236,236,236,0) 70%);
  }
  .brand {
    position: absolute;
    display: flex;
    align-items: center;
    gap: 8px;
    text-transform: uppercase;
    color: var(--ink);
    white-space: nowrap;
  }
  .brand-dot {
    width: 12px; height: 12px;
    border-radius: 50%;
    background: var(--gold);
    flex: none;
  }

  /* front */
  .card-front .ornament { left: 150px; top: 20px; width: 240px; height: 130px; }
  .card-front .brand { left: 50%; top: 92px; transform: translateX(-50%); font-size: 13px; letter-spacing: 3px; }
  .services {
    position: absolute;
    left: 0; right: 0; top: 150px;
    list-style: none;
    text-align: center;
    font-size: 15px;
    line-height: 1.55;
  }
  .services .mark { margin-right: 4px; }

  /* back */
  .card-back .ornament { left: 130px; top: 10px; width: 220px; height: 110px; }
  .card-back .brand { left: 110px; top: 58px; font-size: 11px; letter-spacing: 1.8px; }
  .holder { position: absolute; left: 26px; top: 108px; }
  .holder-name {
    font-family: "Pinyon Script", cursive;
    font-size: 30px;
    font-weight: 400;
    line-height: 1;
    color: var(--ink);
  }
  .holder-role { margin-top: 8px; font-size: 13.5px; line-height: 1.15; }
  .contacts {
    position: absolute;
    left: 26px; top: 206px;
    list-style: none;
    font-size: 14px;
    line-height: 1.45;
  }
  .contacts li { display: flex; align-items: center; gap: 8px; }
  .contacts svg { width: 12px; height: 12px; flex: none; fill: var(--ink); }
  .tagline {
    position: absolute;
    right: 16px; top: 158px;
    width: 120px;
    font-size: 13px;
    line-height: 1.35;
    color: var(--card-white);
  }
</style>
</head>
<body>

<section class="card card-front" aria-label="Business card front">
  <svg class="card-art" viewBox="0 0 520 300" preserveAspectRatio="none" aria-hidden="true">
    <defs>
      <linearGradient id="goldBandFront" x1="0" y1="0" x2="1" y2="0">
        <stop offset="0" stop-color="#8a6a22"/>
        <stop offset=".45" stop-color="#f3d98a"/>
        <stop offset="1" stop-color="#c9a24a"/>
      </linearGradient>
    </defs>
    <path d="M0 300 L0 292 C180 286 360 262 520 236 L520 300 Z" fill="#0d0d0d"/>
    <path d="M0 292 C180 286 360 262 520 236 L520 246 C360 272 180 294 0 300 Z" fill="url(#goldBandFront)"/>
  </svg>
  <div class="ornament" role="img" aria-label="Faint floral ornament behind the brand name"></div>
  <div class="brand"><span class="brand-dot"></span>DM Space Arranging Pty Ltd</div>
  <ul class="services">
    <li><span class="mark">»</span>Staging Houses for Sale <span class="mark">»</span>Minor Home Renovations</li>
    <li><span class="mark">»</span>Home Styling &amp; Project Management</li>
    <li><span class="mark">»</span>Re-Designing Rooms for the Disabled</li>
  </ul>
</section>

<section class="card card-back" aria-label="Business card back">
  <svg class="card-art" viewBox="0 0 520 300" preserveAspectRatio="none" aria-hidden="true">
    <defs>
      <linearGradient id="goldSwoosh" x1="0" y1="1" x2="1" y2="0">
        <stop offset="0" stop-color="#8a6a22"/>
        <stop offset=".5" stop-color="#f3d98a"/>
        <stop offset="1" stop-color="#c9a24a"/>
      </linearGradient>
    </defs>
    <path d="M520 0 L480 0 C415 35 385 105 355 175 C325 245 285 282 240 300 L520 300 Z" fill="#0d0d0d"/>
    <path d="M466 4 C405 40 372 108 342 178 C312 248 262 284 30 294" fill="none" stroke="url(#goldSwoosh)" stroke-width="3"/>
    <path d="M452 10 C395 46 360 112 330 180 C300 250 250 282 20 288" fill="none" stroke="url(#goldSwoosh)" stroke-width="1.5"/>
    <path d="M0 295 C120 293 200 292 270 282 L250 300 L0 300 Z" fill="url(#goldSwoosh)"/>
  </svg>
  <div class="ornament" role="img" aria-label="Faint floral ornament behind the brand name"></div>
  <div class="brand"><span class="brand-dot"></span>DM Space Arranging Pty Ltd</div>

  <div class="holder">
    <h1 class="holder-name">Marnie Tulloch</h1>
    <p class="holder-role">B.Com LMR HTV<br>Property Stylist &amp;<br>Project Manager</p>
  </div>

  <ul class="contacts">
    <li>
      <svg viewBox="0 0 24 24"><path d="M6.6 10.8a15.1 15.1 0 0 0 6.6 6.6l2.2-2.2a1 1 0 0 1 1-.25 11.4 11.4 0 0 0 3.6.57 1 1 0 0 1 1 1V20a1 1 0 0 1-1 1A17 17 0 0 1 3 4a1 1 0 0 1 1-1h3.5a1 1 0 0 1 1 1c0 1.25.2 2.45.57 3.6a1 1 0 0 1-.25 1z"/></svg>
      00 00 000 00 0
    </li>
    <li>
      <svg viewBox="0 0 24 24"><path d="M2 5h20v14H2V5zm2 2v.2l8 6.2 8-6.2V7H4zm0 2.7V17h16V9.7l-8 6.2-8-6.2z"/></svg>
      yourname@yourwebsite.com
    </li>
    <li>
      <svg viewBox="0 0 24 24"><path d="M12 2a10 10 0 1 0 0 20 10 10 0 0 0 0-20zm0 2c.9 0 2.2 1.8 2.8 5H9.2C9.8 5.8 11.1 4 12 4zM4.3 11h3.8a17 17 0 0 0 0 2H4.3a8 8 0 0 1 0-2zm5 0h5.4a15 15 0 0 1 0 2H9.3a15 15 0 0 1 0-2zm6.6 0h3.8a8 8 0 0 1 0 2h-3.8a17 17 0 0 0 0-2zM9.2 15h5.6c-.6 3.2-1.9 5-2.8 5s-2.2-1.8-2.8-5z"/></svg>
      www.yourwebsite.com
    </li>
  </ul>

  <p class="tagline">Dramatically Increase the Value of Your Home</p>
</section>

</body>
</html>
```